Poster for a Bicycle show/Expo

We need a poster for a Bicycle show/Expo and sustainable transport. Exhibitors will sell bikes, cycling clothing, accessories, etc. ...
This show is annual and the Poster is for the 2015 edition.

The style must be modern, dynamic, bright colors.

Your concept must be compatible in a landscape format. (We will ourselves adaptations of different formats.)
Width: 210 mm
Height: 297 mm
It's necessary for us to have the source file (vector) for make, later, the different format (flyers, website, ...)

Content of the Poster:
- 1 big picture (no clip art)
- Big title: « Foire du Rayon » (« Salon » or « Salon du » can be small and « Vélo » big.)
- Subtitle: « et de la mobilité douce »
- Date: « 8, 9 et 10 mai 2015 » or « 8-10 mai 2015 »
- Place: « Halle TRV - Gare de Lunel »
- Text line 1: « www.foire-du-rayon.ch - Entrée gratuite »
- Text line 2« Piste d’essais - Restauration sur place »
- Text line 3: « Ve 8 mai de 17h à 21h - Sa 9 mai de 10h à 20h - Di 10 mai de 10h à 18h »
- Please, leave a zone in the poster for sponsors logos
(The predominant information (most visible) are: « Foire du Rayon » and « 8, 9 et 10 mai 2015 or 8-10 mai 2015 »)

Content of the big picture:
- from a cheap stock, like PixKiosk.com
- a bicycle in action or a detail of a bicycle (or a accessory) (no race bike)
- a modern picture with bright colors.
- if a person is on the picture, we prefer a men
- not an aerial view with cyclists in a landscape.

Some examples of poster of shows - with typo-title worked

http://www.expobassinlutece.com/Temp/IMG/F_a9b3c2d4e5f60718293a4b5c6d7e8f9012345678901_200_296.png

http://qx4m.tornafoire.fr/Data/pvtorn_mer/block/F_7cc1bb9396aef1d5e69283647561f0076457c357c5ea6.pdf
(page 2 of this PDF)

http://salons.rivol-evenements.fr/images/rivol-evenements/foires-salons/phototheque/salon-auto-bourlac/salon-auto-bourlac2012-affiche.jpg

http://www.tirovel.net/blog/wp-content/uploads/2007/03/affiche-salon-du-livre.jpg

http://www.quaimarin-gens.com/wp-content/affiche-cannes-2007.jpg
Updates

Hello,

For information, for your next versions, please, add the text "Piste d'essais".

- Text line 1: « www.foire-du-rayon.ch - Entrée gratuite »
- Text line 2: « Piste d’essais - Restauration sur place »
- Text line 3: « Ve 8 mai de 17h à 21h - Sa 9 mai de 10h à 20h - Di 10 mai de 10h à 18h »

Thanks,
Rodolphe

```html
<!DOCTYPE html>
<html lang="fr">
<head>
<meta charset="utf-8">
<title>Foire du Rayon 2015 – Affiche</title>
<link href="https://fonts.googleapis.com/css2?family=Bebas+Neue&display=swap" rel="stylesheet">
<style>
  :root {
    --backdrop: #d9d9d9;
    --ink: #111111;
    --white: #ffffff;
    --lime: #b3c71a;
    --teal: #5cbfc8;
    --mauve: #a6788f;
    --bar: #323232;
    --sky-top: #6fa9de;
    --sky-mid: #cfe4f3;
    --ground-warm: #d9a66a;
    --ground-dark: #7a6552;
  }
  * { margin: 0; padding: 0; box-sizing: border-box; }
  html, body {
    width: 1200px; height: 1152px; overflow: hidden;
    background: var(--backdrop);
    font-family: "Bebas Neue", "Arial Narrow", sans-serif;
  }
  .poster {
    position: absolute; left: 40px; top: 180px;
    width: 1120px; height: 793px;
    background: var(--white);
    box-shadow: 0 4px 14px rgba(0,0,0,.18);
    overflow: hidden;
  }
  .hero-photo {
    position: absolute; left: 0; top: 0; width: 1120px; height: 667px;
    background:
      linear-gradient(100deg, rgba(255,255,255,.55) 0%, rgba(255,255,255,.15) 38%, rgba(255,255,255,0) 55%),
      linear-gradient(180deg, var(--sky-top) 0%, var(--sky-mid) 55%, var(--ground-warm) 80%, var(--ground-dark) 100%);
  }
  .title-block {
    position: absolute; left: 54px; top: 48px;
    display: flex; align-items: flex-end; gap: 8px;
    color: var(--ink);
  }
  .title-words { display: flex; flex-direction: column; }
  .title-small { font-size: 92px; line-height: .8; letter-spacing: 1px; }
  .title-big { font-size: 212px; line-height: .78; margin-top: 14px; letter-spacing: -1px; }
  .test-track {
    writing-mode: vertical-rl; transform: rotate(180deg);
    font-size: 38px; line-height: 1; letter-spacing: 1px;
    margin-bottom: 4px;
  }
  .subtitle-band {
    position: absolute; left: 0; top: 363px; width: 506px; height: 60px;
    background: var(--lime); color: var(--white);
    font-size: 38px; line-height: 60px; padding-left: 78px; letter-spacing: .5px;
  }
  .event-band {
    position: absolute; left: 0; top: 441px; width: 468px; height: 94px;
    background: var(--teal); color: var(--white);
    font-size: 36px; line-height: 36px; padding: 12px 0 0 78px; letter-spacing: .5px;
  }
  .hours-box {
    position: absolute; left: 964px; top: 442px; width: 156px; height: 108px;
    background: var(--mauve); color: var(--white);
    font-size: 15px; line-height: 19px; padding: 26px 0 0 10px; letter-spacing: .3px;
  }
  .info-bar {
    position: absolute; left: 0; top: 667px; width: 1120px; height: 54px;
    background: var(--bar); color: var(--white);
    font-size: 29px; line-height: 56px; text-align: center; letter-spacing: .5px;
  }
  .sponsor-strip {
    position: absolute; left: 0; top: 721px; width: 1120px; height: 72px;
    display: flex; justify-content: space-around; align-items: center;
    padding: 0 20px;
  }
  .sponsor-name { font-size: 34px; color: var(--ink); letter-spacing: 1px; }
</style>
</head>
<body>
  <main class="poster">
    <div class="hero-photo" role="img" aria-label="Photo en contre-plongée d'un cycliste sur un vélo tout-terrain blanc, roue arrière au premier plan, sur un chemin de terre sous un ciel bleu"></div>

    <header class="title-block">
      <h1 class="title-words">
        <span class="title-small">FOIRE DU</span>
        <span class="title-big">RAYON</span>
      </h1>
      <span class="test-track">PISTE D'ESSAIS</span>
    </header>

    <p class="subtitle-band">ET DE LA MOBILITÉ DOUCE</p>

    <p class="event-band">8-10 MAI 2015<br>HALLE TRV - GARE DE LUNEL</p>

    <p class="hours-box">VE 8 MAI DE 17H À 21H<br>SA 9 MAI DE 10H À 20H<br>DI 10 MAI DE 10H À 18H</p>

    <p class="info-bar">WWW.FOIRE-DU-RAYON.CH - ENTRÉE GRATUITE - RESTAURATION SUR PLACE</p>

    <footer class="sponsor-strip">
      <span class="sponsor-name">KORVAN</span>
      <span class="sponsor-name">LUMEO</span>
      <span class="sponsor-name">TARVI</span>
      <span class="sponsor-name">VELQUO</span>
      <span class="sponsor-name">LUMEO</span>
      <span class="sponsor-name">TARVI</span>
    </footer>
  </main>
</body>
</html>
```